New webdesign for a cable company

We need a new design for Lunor Media.

There exist a suggestion for the page, were we have attached files to show you this. The design here is not good enough, but here you can se what content we need.

You can feel free to give adjustment to this design to make it better, our blow us away with a new brilliant design, but from this design you see what content we need.

The important is that the company get a design who represent its products:
- TV = Cable TV
- Bredbånd = Broadband
- Mobil = Mobile phone
- Strøm = Electricity
- Alarm = Alarm
- Lunor Komplett = a cobain pagage of all our products.

Lunor Media would like costumers who visit the site to het the impression that Lunor Media is a professional, innovative and fun company.
Updates

We have to day uploaded pictures of the existing page as the link haven't been working for the most of you as it's placed on a server our developer are using and is often shut it down. 

We have also updated the brief with some new and updated description so please read true the updated brief. 

We will at the same time inform that we haven't been able to give feedback on any of the received design and are sorry for that, we will within the next 24 hours hopefully have started responded the different received designs.

Looking forward to see more suggestion and hope you will help us create and very professional and informative design. 

Reason: We have decided to extend the deadline due to the number of design suggestion who is sent in and your lack of response to all designers due to our own workload.

This project was unfortunately for different reason put on ice for a while, but we are now ready to complete the design and will answer and give feedback too all the received design suggestions. 

Within a couple of days we hope we have answered all you who sent us suggestions, we appreciate all suggestions and hope to get in more suggestions.

Reason: Deisgn description have been updated

Target Market(s)

Our costumer are both private and companies

Industry/Entity Type

Tv

Requirements
Must have
• A easy way to promote and inform about changes in our products, there are a constant change in our products and it must bee a easy and good way to changes ass the marked change. Cheek out this link, for a example of what we like/think of here, https://nett.fjordsignal.no

On all pages there must be a easy way to click on a order button and too inform about your interest (thats two different things), could be placed in the top right corner for example. In the order form you should follow a step by step part:
1. Cheek what product we can provide you.
2. Chooce products.
3. Costumer inforamtion.
4. Confirmation.

Somewere on the portal it must be possible for costumers to log on to their own administration, where they can cheek for invoices, other statuses, etc.

A main menu existing of:
Hjem (Home)
Produkter (Products)
Storkunde (key account/large costumers)
Kundeservice (Costumerservice)
Min side (My page)

The main menu should have the following sub titles:
- Under "Produkter"/products our different products must be listed
- Under "Kundeservice"/Costumerservice it must have these submenus:
- Hjelp og støtte = Help.
- Faktura = Invoice
- Brukerguider = Userguides
- Abbonementavtaler = Terms and conditions.

A bottom menu where we have 5 main categories, with sub categories:
Om oss (about us)
- Om Lunor Media (about Lunor Media)
- Kontaktinformajson ( contact information)
- Pressemeldinger (Pressrelese)
- Ledige stillinger (positions available)
- KRAV ( and organisastion in our field)

Produkter (Product)
- TV (TV)
- Bredbånd (Broadand)
- Telefoni (telephony, both mobil)
- Strøm (elecricity)
- Arlam (Alarm)

Borrettslag/Sameier (Housing cooperatives)
- Løsninger (solutions)
- Produkter (product)
- Kontaktpersoner (contactpersons)

Utbygger (developer)
- Hva vi kan gjøre for dere. (What we can do for you)

Opperatørnett (operators)

Build up the categories and bottom menu something like this:
https://nett.fjordsignal.no
www.brevix.com
Nice to have
• A main menu existing of:
Hjem (Home)
Produkter (Products)
Lunor Media
Kontakt oss (Contact us)

Under "Produkter"/products our different products must be listed and under "Kundeservice"/Costumerservice it must have these submenus:
- Hjelp og støtte = Help.
- Faktura = Invoice
Should not have
• Any translation section since the homepage only will be in Norwegian.

```html
<!DOCTYPE html>
<html lang="en">
<head>
<meta charset="utf-8">
<title>Lunor Media – Lunor Broadband</title>
<link rel="stylesheet" href="https://fonts.googleapis.com/css2?family=Ubuntu:wght@300;400;500;700&display=swap">
<style>
:root{
  --page:#f2f2f2;
  --white:#ffffff;
  --ink:#555555;
  --text:#666666;
  --muted:#888888;
  --blue:#29b6e8;
  --blue-dark:#1a9fd3;
  --hero:#555555;
  --tabs:#9a9a9a;
  --line:#d9d9d9;
  --soft:#e8e8e8;
}
*{box-sizing:border-box;margin:0;padding:0}
html,body{width:997px;height:1200px;overflow:hidden}
body{background:var(--page);font-family:"Ubuntu",sans-serif;color:var(--text);position:relative}
.abs{position:absolute}
ul{list-style:none}
h1,h2{font-weight:400}

/* header */
.brand{left:118px;top:18px;display:flex;align-items:center;gap:12px}
.brand-dot{width:30px;height:30px;border-radius:50%;background:var(--blue)}
.brand-name{font-size:34px;font-weight:400;color:var(--ink);letter-spacing:-.5px}
.top-nav{left:507px;top:10px;width:373px;height:20px;background:var(--white);display:flex;justify-content:space-around;align-items:center;font-size:11px;text-transform:uppercase}
.top-nav a{color:var(--ink);text-decoration:none}
.top-nav a.current{color:#111}
.search{left:707px;top:42px;width:173px;height:26px;background:var(--white);display:flex;align-items:center;gap:8px;padding-left:8px;font-size:11px;color:var(--muted);text-transform:uppercase}

/* product tabs */
.product-tabs{left:0;top:82px;width:997px;height:35px;background:var(--tabs)}
.product-tabs a{position:absolute;top:0;height:35px;line-height:35px;color:var(--white);text-decoration:none;font-size:13px;text-transform:uppercase;text-align:center}
.product-tabs a.active{background:var(--hero)}

/* hero */
.hero{left:0;top:117px;width:997px;height:353px;background:var(--hero);overflow:hidden}
.hero-art{left:383px;top:0;width:497px;height:353px;background:linear-gradient(180deg,#6a6a6a,#3a3a3a 85%,#a8a8a8)}
.screen{left:464px;top:219px;width:329px;height:207px;background:var(--white)}
.screen-name{left:0;top:44px;width:100%;text-align:center;font-size:32px;color:var(--ink)}
.screen-cta{left:0;top:118px;width:100%;height:59px;background:var(--blue);color:var(--white);font-weight:700;font-size:27px;line-height:59px;text-align:center;letter-spacing:.5px}
.hero-title{left:140px;top:179px;font-size:26px;font-weight:700;color:var(--white);letter-spacing:.5px;white-space:nowrap}
.hero-list{left:140px;top:228px;color:var(--white);font-size:13px}
.hero-list li{height:23.3px;display:flex;align-items:center;gap:7px}
.dots{left:140px;top:437px;display:flex;gap:3px}
.dots span{width:9px;height:9px;background:#8a8a8a}
.dots span.on{background:var(--white)}

/* main column */
.section-title{left:116px;top:510px;width:499px;display:flex;align-items:flex-end;gap:4px;font-size:28px;color:var(--ink);letter-spacing:.5px}
.section-title em{font-style:normal;color:var(--blue)}
.section-title .rule{flex:1;height:1px;background:var(--line);margin-bottom:6px}
.intro{left:116px;top:558px;width:495px;font-size:12.6px;line-height:17.3px}
.intro p+p{margin-top:17px}

.services-head{left:116px;top:722px;height:43px}
.services-head span{position:absolute;left:15px;top:12px;font-size:20px;color:var(--ink);white-space:nowrap}
.services{left:116px;top:765px;width:499px;height:138px;background:var(--white)}
.services ul{position:absolute;top:10px;font-size:13px;color:var(--ink)}
.services li{height:23.3px;display:flex;align-items:center;gap:9px}

.testimonials-title{left:116px;top:928px;font-size:20px;color:var(--blue)}
.avatar{left:117px;top:964px;width:65px;height:65px;background:var(--white);border:1px solid var(--line);padding:5px}
.avatar div{width:100%;height:100%;background:linear-gradient(180deg,#c9a38a,#5a6470)}
.quote{left:203px;top:963px;width:412px;height:167px;background:var(--white);padding:20px 22px;font-size:12.6px;line-height:17px;color:var(--ink)}
.quote::before{content:"";position:absolute;left:-14px;top:14px;border-top:14px solid transparent;border-bottom:14px solid transparent;border-right:14px solid var(--white)}
.quote cite{display:block;margin-top:17px;font-style:normal;color:var(--blue)}

/* sidebar */
.news{left:647px;top:512px;width:233px;height:346px;background:var(--white)}
.news-head{height:41px;background:var(--blue);display:flex;align-items:center;justify-content:space-between;padding:0 7px 0 11px}
.news-head h2{font-size:20px;color:var(--white)}
.news-head a{font-size:9px;background:#7fd6f4;color:var(--white);padding:3px 5px;text-decoration:none}
.news-item{position:relative;height:75.5px;margin:0 11px;border-bottom:1px solid var(--soft)}
.news-item:last-child{border-bottom:0}
.date{position:absolute;left:0;top:13px;width:52px;height:52px;border-radius:50%;background:var(--soft);text-align:center;color:var(--ink);font-weight:500;line-height:1}
.date b{display:block;font-size:19px;margin-top:9px}
.date small{font-size:12px}
.news-item p{position:absolute;left:67px;top:12px;width:145px;font-size:10px;line-height:14px;color:var(--ink)}
.news-item p a{color:var(--blue);text-decoration:none}

.contact-photo{left:792px;top:915px;width:88px;height:188px;background:linear-gradient(180deg,#d8d8d8,#8c8f94)}
.contact-title{left:647px;top:888px;font-size:20px;color:var(--blue);z-index:1}
.contact-name{left:647px;top:929px;font-size:14px;color:#222}
.contact-text{left:645px;top:954px;width:145px;font-size:10px;line-height:14px;color:var(--ink)}
.contact-phone{left:646px;top:1047px;font-size:22px;font-weight:700;color:var(--blue-dark)}
.contact-mail{left:646px;top:1072px;font-size:12px;color:#222}

/* footer */
.footer-rule{left:116px;top:1160px;width:764px;height:1px;background:var(--line)}
.copyright{left:116px;top:1173px;font-size:13px;color:var(--muted)}
.social{left:835px;top:1175px;display:flex;gap:3px}
.social span{width:13px;height:13px;background:#4a7fb5}
.social span:nth-child(2){background:var(--blue)}
.social span:nth-child(3){background:#2d6ea8}
</style>
</head>
<body>

<header>
  <div class="abs brand"><span class="brand-dot"></span><span class="brand-name">Lunor Media</span></div>
  <nav class="abs top-nav">
    <a class="current" href="#">Home</a><a href="#">Products</a><a href="#">Costumer service</a><a href="#">Lunor Media</a><a href="#">Contact us</a>
  </nav>
  <div class="abs search">
    <svg width="14" height="14" viewBox="0 0 14 14"><circle cx="8" cy="6" r="4.5" fill="none" stroke="#888" stroke-width="1.5"/><line x1="4.8" y1="9.2" x2="1" y2="13" stroke="#888" stroke-width="1.8"/></svg>
    Enter your search...
  </div>
</header>

<nav class="abs product-tabs">
  <a href="#" style="left:136px;width:115px">Lunor TV</a>
  <a href="#" class="active" style="left:250px;width:182px">Lunor Broadband</a>
  <a href="#" style="left:440px;width:128px">Lunor Mobile</a>
  <a href="#" style="left:590px;width:122px">Lunor Strom</a>
  <a href="#" style="left:730px;width:126px">Lunor Komplett</a>
</nav>

<section class="abs hero">
  <div class="abs hero-art" role="img" aria-label="Illustration of a laptop hanging among cables and plugs"></div>
</section>
<div class="abs screen">
  <div class="abs screen-name">Lunor Media</div>
  <div class="abs screen-cta">ONLINE ORDER NOW!</div>
</div>
<h1 class="abs hero-title">LUNOR BROADBAND</h1>
<ul class="abs hero-list">
  <li><svg width="12" height="12" viewBox="0 0 12 12"><circle cx="6" cy="6" r="5" fill="none" stroke="#fff" stroke-width="1.4"/><path d="M3.5 6l2 2 4-4.5" fill="none" stroke="#fff" stroke-width="1.6"/></svg>Aenean semper bibendum</li>
  <li><svg width="12" height="12" viewBox="0 0 12 12"><circle cx="6" cy="6" r="5" fill="none" stroke="#fff" stroke-width="1.4"/><path d="M3.5 6l2 2 4-4.5" fill="none" stroke="#fff" stroke-width="1.6"/></svg>Pellentesque quis tortor.</li>
  <li><svg width="12" height="12" viewBox="0 0 12 12"><circle cx="6" cy="6" r="5" fill="none" stroke="#fff" stroke-width="1.4"/><path d="M3.5 6l2 2 4-4.5" fill="none" stroke="#fff" stroke-width="1.6"/></svg>Sed varius tincidunt.</li>
  <li><svg width="12" height="12" viewBox="0 0 12 12"><circle cx="6" cy="6" r="5" fill="none" stroke="#fff" stroke-width="1.4"/><path d="M3.5 6l2 2 4-4.5" fill="none" stroke="#fff" stroke-width="1.6"/></svg>Sed nec varius eu sed turpis.</li>
  <li><svg width="12" height="12" viewBox="0 0 12 12"><circle cx="6" cy="6" r="5" fill="none" stroke="#fff" stroke-width="1.4"/><path d="M3.5 6l2 2 4-4.5" fill="none" stroke="#fff" stroke-width="1.6"/></svg>Pellentesque quis tortor.</li>
</ul>
<div class="abs dots"><span class="on"></span><span></span><span></span><span></span><span></span></div>

<main>
  <h2 class="abs section-title"><span><em>LUNOR</em> BROADBAND</span><span class="rule"></span></h2>
  <div class="abs intro">
    <p>This is the studio's version of Lorem Ipsum. Proin gravida nibh vel velit auctor aliquet. Aenean sollicitudin, lorem quis bibendum auctor, nisi elit consequat ipsum, nec sagittis sem nibh id elit. Duis sed odio sit amet nibh vulputate cursus a sit amet mauris. Morbi accumsan ipsum velit.</p>
    <p>Nam nec tellus a odio tincidunt auctor a ornare odio. Sed non mauris vitae erat consequat auctor eu in elit. Class aptent taciti sociosqu ad litora torquent per conubia nostra, per inceptos himenaeos.</p>
  </div>

  <div class="abs services-head">
    <svg width="312" height="43" viewBox="0 0 312 43"><path d="M10 0H282L312 43H0V10Q0 0 10 0Z" fill="#e8e8e8"/></svg>
    <span>LUNOR BROADBAND SERVICES</span>
  </div>
  <div class="abs services">
    <ul style="left:17px">
      <li><svg width="12" height="12" viewBox="0 0 12 12"><circle cx="6" cy="6" r="5" fill="none" stroke="#c8c8c8" stroke-width="1.3"/><path d="M3.5 6l2 2 4-4.5" fill="none" stroke="#c8c8c8" stroke-width="1.5"/></svg>Aenean semper bibendum</li>
      <li><svg width="12" height="12" viewBox="0 0 12 12"><circle cx="6" cy="6" r="5" fill="none" stroke="#c8c8c8" stroke-width="1.3"/><path d="M3.5 6l2 2 4-4.5" fill="none" stroke="#c8c8c8" stroke-width="1.5"/></svg>Pellentesque quis tortor.</li>
      <li><svg width="12" height="12" viewBox="0 0 12 12"><circle cx="6" cy="6" r="5" fill="none" stroke="#c8c8c8" stroke-width="1.3"/><path d="M3.5 6l2 2 4-4.5" fill="none" stroke="#c8c8c8" stroke-width="1.5"/></svg>Sed varius tincidunt.</li>
      <li><svg width="12" height="12" viewBox="0 0 12 12"><circle cx="6" cy="6" r="5" fill="none" stroke="#c8c8c8" stroke-width="1.3"/><path d="M3.5 6l2 2 4-4.5" fill="none" stroke="#c8c8c8" stroke-width="1.5"/></svg>Sed nec varius eu sed turpis.</li>
      <li><svg width="12" height="12" viewBox="0 0 12 12"><circle cx="6" cy="6" r="5" fill="none" stroke="#c8c8c8" stroke-width="1.3"/><path d="M3.5 6l2 2 4-4.5" fill="none" stroke="#c8c8c8" stroke-width="1.5"/></svg>Pellentesque quis tortor.</li>
    </ul>
    <ul style="left:257px">
      <li><svg width="12" height="12" viewBox="0 0 12 12"><circle cx="6" cy="6" r="5" fill="none" stroke="#c8c8c8" stroke-width="1.3"/><path d="M3.5 6l2 2 4-4.5" fill="none" stroke="#c8c8c8" stroke-width="1.5"/></svg>Aenean semper ante bibendum.</li>
      <li><svg width="12" height="12" viewBox="0 0 12 12"><circle cx="6" cy="6" r="5" fill="none" stroke="#c8c8c8" stroke-width="1.3"/><path d="M3.5 6l2 2 4-4.5" fill="none" stroke="#c8c8c8" stroke-width="1.5"/></svg>Pellentesque or ac quis tortor.</li>
      <li><svg width="12" height="12" viewBox="0 0 12 12"><circle cx="6" cy="6" r="5" fill="none" stroke="#c8c8c8" stroke-width="1.3"/><path d="M3.5 6l2 2 4-4.5" fill="none" stroke="#c8c8c8" stroke-width="1.5"/></svg>Sed varius vitae tincidunt.</li>
      <li><svg width="12" height="12" viewBox="0 0 12 12"><circle cx="6" cy="6" r="5" fill="none" stroke="#c8c8c8" stroke-width="1.3"/><path d="M3.5 6l2 2 4-4.5" fill="none" stroke="#c8c8c8" stroke-width="1.5"/></svg>Sed nec leo eu sed turpis.</li>
      <li><svg width="12" height="12" viewBox="0 0 12 12"><circle cx="6" cy="6" r="5" fill="none" stroke="#c8c8c8" stroke-width="1.3"/><path d="M3.5 6l2 2 4-4.5" fill="none" stroke="#c8c8c8" stroke-width="1.5"/></svg>Sed varius vitae tincidunt.</li>
    </ul>
  </div>

  <h2 class="abs testimonials-title">TESTIMONIALS</h2>
  <div class="abs avatar"><div role="img" aria-label="Portrait photo of the client"></div></div>
  <blockquote class="abs quote">
    This is the studio's version of Lorem Ipsum. Proin gravida nibh vel velit auctor aliquet. Aenean sollicitudin, lorem quis bibendum auctor, nisi elit consequat ipsum, nec sagittis sem nibh id elit. Duis sed odio sit amet nibh vulputate cursus a sit amet mauris. Morbi accumsan ipsum velit. Nam nec tellus a odio tincidunt auctor a ornare odio.
    <cite>- Client's Name</cite>
  </blockquote>
</main>

<aside>
  <section class="abs news">
    <div class="news-head"><h2>NEWS</h2><a href="#">All News</a></div>
    <article class="news-item"><div class="date"><b>22</b><small>JAN</small></div><p>This is the studio's version of nibh vel velit auctor aliquet. <a href="#">[Readmore...]</a></p></article>
    <article class="news-item"><div class="date"><b>25</b><small>DEC</small></div><p>This is the studio's version of nibh vel velit auctor aliquet. <a href="#">[Readmore...]</a></p></article>
    <article class="news-item"><div class="date"><b>18</b><small>APR</small></div><p>This is the studio's version of nibh vel velit auctor aliquet. <a href="#">[Readmore...]</a></p></article>
    <article class="news-item"><div class="date"><b>29</b><small>MAR</small></div><p>This is the studio's version of nibh vel velit auctor aliquet. <a href="#">[Readmore...]</a></p></article>
  </section>

  <div class="abs contact-photo" role="img" aria-label="Photo of a smiling customer service representative in a suit"></div>
  <h2 class="abs contact-title">CONTACT INFO</h2>
  <div class="abs contact-name">Lunor Media</div>
  <p class="abs contact-text">This is the studio's version of Lorem Ipsum. Proin gravida nibh vel velit auctor aliquet.</p>
  <div class="abs contact-phone">47318260</div>
  <div class="abs contact-mail">post@lunormedia.no</div>
</aside>

<footer>
  <div class="abs footer-rule"></div>
  <p class="abs copyright">Copyright ©2013 Lunor Media. All Rights Reserved.</p>
  <div class="abs social"><span></span><span></span><span></span></div>
</footer>

</body>
</html>
```